Webdesign für Kleingruppenreisen in die Südsteiermark
Zielgruppe
Wir sind ein Start-Up Unternehmen, das als Kleingruppenreisen in die Südsteiermark veranstaltet; der Schwerpunkt liegt auf dem Kulinarischen. Zielgruppe sind Geschäftsleute, die diese Kurzreisen (Do-So) für Marketingzwecke oder als Mitarbeiterbonus (oder auch privat) nutzen möchten.
Aufgabenstellung
Die Homepage soll eine Online-Shop Möglichkeit bieten, in der die Reise (bisher gibt es nur einen Ablauf) gebucht werden kann. Optisch sollte sie sich an das bereits von Ihnen erstellte Logo anlehnen und möglichst ansprechende Fotos von der Südsteiermark, Graz, Leoben usw. enthalten. (Siehe die beiden Flyer und das Logo)
Wir haben inzwischen Bildfreigaben von Haldauer und dem Tourismusverband Kellwinden erhalten und können auch eigene Bilder zur Verfügung stellen. Bitte kontaktieren Sie uns dafür, wenn nötig.

```html
<!DOCTYPE html>
<html lang="de">
<head>
<meta charset="utf-8">
<title>GenussPfade Reisen – Reisen für Feinschmecker in die Steiermark</title>
<link href="https://fonts.googleapis.com/css2?family=Lato:ital,wght@0,300;0,400;0,700;1,300;1,700;1,900&display=swap" rel="stylesheet">
<style>
:root{
  --cream:#fef3eb;
  --white:#ffffff;
  --text:#333333;
  --heading:#3a3a3a;
  --teal:#7fd0d8;
  --red:#c8202b;
  --green:#5aa35a;
  --shadow:rgba(0,0,0,.28);
}
*{box-sizing:border-box;margin:0;padding:0}
html,body{width:1200px;height:2479px;overflow:hidden;background:var(--white);font-family:'Lato',sans-serif;color:var(--text)}
.page{position:relative;width:1200px;height:2479px}
.site-header{position:absolute;left:0;top:0;width:1200px;height:196px;background:var(--cream);border-bottom:6px solid #b9b4b0}
.nav-link{position:absolute;top:151px;font-size:15px;color:var(--text);text-decoration:none}
.brand{position:absolute;left:470px;top:40px;width:280px;height:130px;display:flex;flex-direction:column;align-items:center;justify-content:center;gap:6px}
.brand-mark{width:26px;height:26px;border-radius:50%;background:var(--red)}
.brand-name{font-size:30px;font-weight:700;color:var(--red);letter-spacing:.5px;white-space:nowrap}
.brand-sub{font-size:12px;color:var(--text);white-space:nowrap}
.hero{position:absolute;left:0;width:1200px}
.hero-vineyard{top:196px;height:452px;background:linear-gradient(180deg,#cfe3f3 0%,#a9c4d0 35%,#6f8f4c 55%,#4f7a2c 80%,#3e6320 100%)}
.hero-wine{top:1434px;height:447px;background:linear-gradient(100deg,#8a6a40 0%,#6b8c6a 30%,#5b7f90 45%,#789850 70%,#c9b88a 85%,#7a9a3a 100%)}
.hero-box{position:absolute;left:165px;width:456px;height:187px;background:rgba(255,255,255,.45);text-align:center}
.hero-title{font-size:36px;font-weight:900;font-style:italic;color:var(--heading);line-height:46px;padding-top:14px}
.btn{position:absolute;left:50%;transform:translateX(-50%);height:52px;border-radius:10px;background:var(--teal);color:var(--white);font-size:27px;font-weight:300;font-style:italic;line-height:52px;text-decoration:none;white-space:nowrap}
.content{position:absolute;left:150px;width:900px;background:var(--cream)}
.card{position:absolute;width:246px;height:272px;background:var(--white);box-shadow:0 2px 4px var(--shadow);font-size:12.8px;line-height:21.7px}
.card-icon{position:absolute;left:93px;top:7px;width:60px;height:60px;border-radius:50%;background:var(--white);box-shadow:0 1px 4px var(--shadow);display:flex;align-items:center;justify-content:center}
.card-text{position:absolute;top:78px;left:7px;white-space:nowrap}
.card-text p+p{margin-top:5px}
.taste-list{list-style:none}
.taste-list li{position:relative;padding-left:16px;margin-top:6.8px}
.taste-list li::before{content:"";position:absolute;left:1px;top:5px;width:8px;height:8px;border-radius:50% 50% 50% 0;transform:rotate(-45deg);background:var(--green)}
.brand-large{position:absolute;left:0;top:380px;width:900px;text-align:center}
.brand-large .brand-name{font-size:86px;display:block}
.brand-large .brand-sub{font-size:34px;display:block;margin-top:14px}
.site-footer{position:absolute;left:0;top:2213px;width:1200px;height:266px;background:var(--cream);border-top:4px solid #a9a5a2}
.newsletter{position:absolute;left:165px;top:22px;width:870px;height:50px;background:var(--white);border-radius:6px;box-shadow:0 2px 4px var(--shadow)}
.news-field{position:absolute;left:8px;top:7px;width:232px;height:37px;border:1px solid #cfcfcf;display:flex}
.news-icon{width:50px;border-right:1px solid #cfcfcf;display:flex;align-items:center;justify-content:center}
.news-input{padding-left:24px;font-size:11px;color:#999;line-height:37px}
.news-title{position:absolute;left:287px;top:7px;font-size:18px;color:var(--red)}
.news-sub{position:absolute;left:287px;top:30px;font-size:11px;color:var(--text);white-space:nowrap}
.footer-col{position:absolute;top:100px;font-size:14px;line-height:21.7px}
.footer-col h3{font-size:14px;font-weight:400;color:var(--red);margin-bottom:4px}
.footer-col a{display:block;color:var(--text);text-decoration:none;letter-spacing:.3px}
</style>
</head>
<body>
<div class="page">

<header class="site-header">
  <a class="nav-link" style="left:239px" href="#">Start</a>
  <a class="nav-link" style="left:330px" href="#">Reise buchen</a>
  <div class="brand"><span class="brand-mark"></span><span class="brand-name">GenussPfade Reisen</span><span class="brand-sub">Reisen für Feinschmecker in die Steiermark</span></div>
  <a class="nav-link" style="left:810px" href="#">Kontakt</a>
  <a class="nav-link" style="left:922px" href="#">Impressum</a>
</header>

<section class="hero hero-vineyard" role="img" aria-label="Foto: Weinberge der Südsteiermark mit Klapotetz vor hügeliger Landschaft">
  <div class="hero-box" style="top:98px">
    <h1 class="hero-title">Haben Sie Geschmack<br>am Besonderen?</h1>
    <a class="btn" href="#" style="top:117px;width:218px">Reise buchen</a>
  </div>
</section>

<section class="content" style="top:648px;height:774px">
  <article class="card" style="left:16px;top:28px">
    <div class="card-icon"><svg width="30" height="30" viewBox="0 0 30 30"><path d="M3 8h10l-1 6a4 4 0 0 1-8 0z M8 18v7 M5 25h6" fill="none" stroke="#7fd0d8" stroke-width="2"/><rect x="18" y="10" width="7" height="16" rx="2" fill="#7fd0d8"/><rect x="20" y="3" width="3" height="8" fill="#7fd0d8"/></svg></div>
    <div class="card-text" style="left:22px">
      <p>Lieben Sie...</p>
      <ul class="taste-list">
        <li>gutes Essen?</li>
        <li>hervorragendes Bier?</li>
        <li>exquisiten Wein?</li>
        <li>kulinarische Spezialitäten?</li>
        <li>und gastfreundliche Menschen?</li>
        <li>wunderschöne Landschaften?</li>
      </ul>
    </div>
  </article>
  <article class="card" style="left:327px;top:28px">
    <div class="card-icon"><svg width="34" height="26" viewBox="0 0 34 26"><path d="M17 2c4 5 4 14 0 20c-4-6-4-15 0-20z M8 6c5 2 8 9 8 16c-6-2-9-8-8-16z M26 6c1 8-2 14-8 16c0-7 3-14 8-16z M2 12c3 0 6 5 11 10c-6 0-10-4-11-10z M32 12c-1 6-5 10-11 10c5-5 8-10 11-10z" fill="#7fd0d8"/></svg></div>
    <div class="card-text"><p>Wir glauben, dass unsere Reisen<br>hervorragende Möglichkeiten zum<br>Entspannen und Genießen bieten<br>und sich deshalb besonders gut als<br>„Schmankerl“ für umsatzstarke Kunden,<br>erfolgreiche Mitarbeiter oder einfach<br>für Sie selbst und Ihre Freunde eignen.</p></div>
  </article>
  <article class="card" style="left:639px;top:28px">
    <div class="card-icon"><svg width="34" height="22" viewBox="0 0 34 22"><path d="M2 12l4-1 3 3 7-2-6-9 3-1 10 8 7-2c2 0 3 2 1 3l-23 7z" fill="#7fd0d8"/></svg></div>
    <div class="card-text" style="left:10px"><p>Lassen Sie das hektische Berlin und das<br>flache Land für ein paar Tage hinter<br>sich!<br>Die südlichen Ausläufer der Alpen und<br>die sogenannte „steirische Toskana“<br>sind nur 90 Minuten Direktflug<br>entfernt.</p></div>
  </article>
  <div class="brand-large"><span class="brand-name">GenussPfade Reisen</span><span class="brand-sub">Reisen für Feinschmecker in die Steiermark</span></div>
</section>

<section class="hero hero-wine" role="img" aria-label="Foto: Wein wird vor sonniger Landschaft in zwei Gläser gegossen, die anstoßen">
  <div class="hero-box" style="top:132px">
    <h2 class="hero-title">Sind Sie auf den<br>Geschmack gekommen?</h2>
    <a class="btn" href="#" style="top:117px;width:262px">kontaktieren Sie uns</a>
  </div>
</section>

<section class="content" style="top:1881px;height:323px">
  <article class="card" style="left:16px;top:29px">
    <div class="card-icon"><svg width="26" height="30" viewBox="0 0 26 30"><path d="M7 3v25" stroke="#7fd0d8" stroke-width="2.5"/><path d="M8 4l14 4-14 6z" fill="#7fd0d8"/><ellipse cx="7" cy="28" rx="5" ry="1.5" fill="#7fd0d8"/></svg></div>
    <div class="card-text" style="left:10px"><p>Lernen Sie Leoben, die Hauptstadt des<br>Haldauer-Bieres kennen und erfahren Sie<br>in der Haldauer-Welt die Geschichte<br>dieses weltbekannten Gebräus.</p></div>
  </article>
  <article class="card" style="left:327px;top:29px">
    <div class="card-icon"><svg width="34" height="34" viewBox="0 0 34 34"><circle cx="17" cy="17" r="8" fill="#7fd0d8"/><g stroke="#7fd0d8" stroke-width="3" stroke-linecap="round"><path d="M17 2v4M17 28v4M2 17h4M28 17h4M6.5 6.5l3 3M24.5 24.5l3 3M6.5 27.5l3-3M24.5 9.5l3-3"/></g></svg></div>
    <div class="card-text" style="left:6px"><p>Entdecken Sie Graz, die abwechslungs-<br>reiche Landeshauptstadt und Kultur-<br>hauptstadt 2003, mit ihren vielfältigen<br>kulturellen Angeboten, den charmanten<br>Gassen und atemberaubenden Ausblicken.</p><p>Genießen Sie die südlichere Sonne und<br>kosten Sie die ausgezeichneten Weine<br>der Winzer in der Buschenschank.</p></div>
  </article>
  <article class="card" style="left:639px;top:29px">
    <div class="card-icon"><svg width="38" height="28" viewBox="0 0 38 28"><rect x="6" y="3" width="26" height="10" rx="2" fill="#7fd0d8"/><rect x="2" y="14" width="34" height="10" rx="2" fill="#7fd0d8"/><rect x="9" y="7" width="20" height="4" rx="1" fill="#fff"/></svg></div>
    <div class="card-text" style="left:7px"><p>Während unser Exklusiv Transfer Sie zu<br>den Sehenswürdigkeiten bringt, lüftet<br>unser steirischer Reiseleiter für Sie die<br>Geheimnisse seines Heimatlandes, des<br>„grünen Herzens Österreichs“ und führt<br>Sie in erstklassige Restaurants.</p><p>Sie wohnen in ausgesuchten Hotels in<br>zentraler Lage.</p></div>
  </article>
</section>

<footer class="site-footer">
  <div class="newsletter">
    <div class="news-field">
      <div class="news-icon"><svg width="28" height="20" viewBox="0 0 28 20"><rect width="28" height="20" rx="2" fill="#d8262f"/><path d="M1 2l13 10L27 2M1 18l9-8M27 18l-9-8" fill="none" stroke="#fff" stroke-width="1.6"/></svg></div>
      <div class="news-input">Ihre E-Mail Adresse</div>
    </div>
    <div class="news-title">Newsletter</div>
    <div class="news-sub">Abonnieren Sie unseren kostenlosen Newsletter und verpasse keine Neuigkeiten</div>
  </div>
  <div class="footer-col" style="left:165px">
    <h3>Telefon</h3>
    <a>XXXXXXXXXX</a><a>Montag bis Freitag</a><a>von XX bis XX Uhr</a>
  </div>
  <div class="footer-col" style="left:448px">
    <h3>Service</h3>
    <a href="#">Kontakt</a><a href="#">&nbsp;Zahlungsbedingungen</a><a href="#">AGB</a><a href="#">Widerrufsrecht</a><a href="#">Widerrufsformular</a><a href="#">Partnerprogramm</a>
  </div>
  <div class="footer-col" style="left:747px">
    <h3>Informationen</h3>
    <a href="#">Über uns</a><a href="#">Datenschutz</a><a href="#">Impressum</a><a href="#">Newsletter</a>
  </div>
</footer>

</div>
</body>
</html>
```